Business Card Design Project

We need a Business Card for an Mechanical Engineering firm in Singapore. The design should be Modern & Technical looking, yet eye catching.

Our company deals in Cutting Tools & Machine Accessories for the Manufacturing Industries such as Oil & Gas, Aero Space, etc... For more information on our Company, you can either email me or view our website www.torvalen.com.sg.

We are trying to revamp our image to give our consumers a fresh new perspective to our company, so we welcome all ideas.

Industry/Entity Type

Business

Requirements
Must have
• Must incorporate New Company Logo into the card as shown in Uploaded file.

```html
<!DOCTYPE html>
<html lang="en">
<head>
<meta charset="utf-8">
<title>Torvalen Tools Business Card</title>
<link rel="stylesheet" href="https://fonts.googleapis.com/css2?family=Cabin:wght@400;500&family=Open+Sans:ital,wght@1,700&display=swap">
<style>
  :root {
    --maroon: #8c1a33;
    --maroon-deep: #3e111f;
    --maroon-mid: #6e1a2e;
    --ink: #3a1820;
    --paper: #ffffff;
    --backdrop: #ece8e6;
    --rule: #b89aa0;
  }
  * { box-sizing: border-box; margin: 0; padding: 0; }
  html, body { width: 1200px; height: 900px; overflow: hidden; }
  body {
    background: var(--backdrop);
    font-family: "Cabin", "Trebuchet MS", sans-serif;
    position: relative;
  }
  .card {
    position: absolute;
    left: 290px;
    width: 620px;
    height: 378px;
    border-radius: 18px;
    overflow: hidden;
    box-shadow: 0 6px 14px rgba(0,0,0,.22);
  }
  .card--front { top: 52px; background: var(--paper); }
  .card--back {
    top: 472px;
    background: radial-gradient(ellipse at 50% 45%, #8a1c35 0%, #5a1628 45%, var(--maroon-deep) 100%);
  }

  .holder { position: absolute; left: 68px; top: 138px; }
  .holder__name {
    font-family: "Open Sans", Arial, sans-serif;
    font-style: italic; font-weight: 700;
    color: var(--maroon); font-size: 19px; letter-spacing: -.2px;
  }
  .holder__role { color: var(--ink); font-size: 17px; margin-top: 3px; }
  .divider {
    position: absolute; left: 34px; top: 190px; width: 288px; height: 1px;
    background: linear-gradient(90deg, var(--rule), rgba(184,154,160,.1));
  }
  .contacts { position: absolute; left: 68px; top: 204px; list-style: none; color: var(--ink); font-size: 17px; line-height: 23.5px; }
  .contacts li { display: flex; align-items: flex-start; }
  .contacts svg { width: 18px; height: 18px; margin: 3px 6px 0 -2px; flex: none; }
  .contacts .indent { padding-left: 22px; }

  .brand {
    position: absolute; display: flex; align-items: center;
    color: var(--maroon); font-family: "Cabin", sans-serif; font-weight: 500;
    text-transform: uppercase; white-space: nowrap;
  }
  .brand__dot { border-radius: 50%; background: currentColor; flex: none; }
  .brand--front { right: 52px; top: 96px; font-size: 25px; letter-spacing: 1px; gap: 10px; }
  .brand--front .brand__dot { width: 18px; height: 18px; }
  .brand--back {
    left: 0; right: 0; justify-content: center; top: 168px;
    color: #f3e6e9; font-size: 48px; letter-spacing: 2px; gap: 18px;
  }
  .brand--back .brand__dot { width: 34px; height: 34px; background: #b42a47; }

  .web-band {
    position: absolute; left: 0; bottom: 0; width: 100%; height: 51px;
    background: radial-gradient(ellipse at 50% 30%, #9a1f3a 0%, var(--maroon-mid) 55%, #561527 100%);
    display: flex; align-items: center; justify-content: center;
  }
  .web-band__url {
    font-family: "Open Sans", Arial, sans-serif; font-style: italic; font-weight: 700;
    color: #fff; font-size: 19px; letter-spacing: .6px;
  }
</style>
</head>
<body>
  <section class="card card--front" aria-label="Card front">
    <div class="brand brand--front"><span class="brand__dot"></span>Torvalen Tools</div>

    <div class="holder">
      <p class="holder__name">Fname Lname</p>
      <p class="holder__role">Company Position</p>
    </div>
    <div class="divider"></div>

    <ul class="contacts">
      <li>
        <svg viewBox="0 0 18 18" aria-hidden="true"><rect x="4" y="2" width="10" height="15" rx="1.5" fill="#8c1a33"/><rect x="6" y="4" width="6" height="4" fill="#fff"/><g fill="#fff"><rect x="6" y="10" width="1.6" height="1.4"/><rect x="8.2" y="10" width="1.6" height="1.4"/><rect x="10.4" y="10" width="1.6" height="1.4"/><rect x="6" y="12.6" width="1.6" height="1.4"/><rect x="8.2" y="12.6" width="1.6" height="1.4"/><rect x="10.4" y="12.6" width="1.6" height="1.4"/></g></svg>
        <span>123-456-7890</span>
      </li>
      <li>
        <svg viewBox="0 0 18 18" aria-hidden="true"><rect x="1.5" y="4" width="15" height="10" fill="none" stroke="#8c1a33" stroke-width="1.3"/><path d="M1.5 4 9 10.5 16.5 4M1.5 14 7 9M16.5 14 11 9" fill="none" stroke="#8c1a33" stroke-width="1.1"/></svg>
        <span>name@torvalen.com.sg</span>
      </li>
      <li>
        <svg viewBox="0 0 18 18" aria-hidden="true"><path d="M1 9 9 2l8 7" fill="none" stroke="#8c1a33" stroke-width="1.6"/><rect x="4" y="9" width="10" height="8" fill="none" stroke="#8c1a33" stroke-width="1.3"/><rect x="7.5" y="12" width="3" height="5" fill="#8c1a33"/></svg>
        <span>27 Kestrel Loop #03-12, Meridian Works</span>
      </li>
      <li class="indent"><span>Hub, Singapore 609871</span></li>
    </ul>

    <div class="web-band"><span class="web-band__url">www.torvalen.com.sg</span></div>
  </section>

  <section class="card card--back" aria-label="Card back">
    <div class="brand brand--back"><span class="brand__dot"></span>Torvalen Tools</div>
  </section>
</body>
</html>
```